Flyer for the Radiant Harvest Worship Day

I am looking to create a flyer for a one day prayer retreat our church is organizing.
This flyer will be posted on social media, websites and will also be printed so it can be mailed to people.
I am looking for something professional, with good use of our logo and band colors (logo colors).
I am counting on the designer's skill, creativity, art and knowledge of media communication to produce a flyer that will effectively and quickly convey the message we are trying to spread.
CONTENT OF THE FLYER:
Event title: Radiant Harvest Worship Day
Date: Tuesday July 2nd, 2019
Time: 11:00AM - 7:00PM
Belmora Hotel, 4875 Wexley Avenue, Portland, Maine 04102 (Room: Juniper)
Event Key words to highlight what the event is about: Prayer, Sharing the Word, Panel discussion, prophecy, Impartation.
Key phrases:
A one day prayer retreat.
Jesus Chris is Lord
Contact info:
www.tolvex.org
Phone: 207 555 3184
Email: contact@brookhavenfold.org

```html
<!DOCTYPE html>
<html lang="en">
<head>
<meta charset="utf-8">
<title>Radiant Harvest Worship Day</title>
<link rel="stylesheet" href="https://fonts.googleapis.com/css2?family=Cinzel:wght@400;700&family=Lato:ital,wght@0,400;0,700;0,900;1,700;1,900&display=swap">
<style>
  :root {
    --navy: #0f3558;
    --navy-deep: #0b2a47;
    --orange: #f3861c;
    --orange-deep: #e8620e;
    --gold: #f7b21c;
    --cream: #f7f1e8;
    --white: #ffffff;
    --stage: #2e2e2e;
  }
  * { margin: 0; padding: 0; box-sizing: border-box; }
  html, body {
    width: 902px; height: 1200px; overflow: hidden;
    background: var(--stage);
  }
  .flyer {
    position: absolute; left: 25px; top: 2px;
    width: 709px; height: 996px;
    transform: scale(1.2); transform-origin: top left;
    overflow: hidden;
    font-family: "Lato", Arial, sans-serif;
    background: var(--cream);
  }
  .flyer-shapes { position: absolute; inset: 0; }
  .brand {
    position: absolute; left: 400px; top: 100px; width: 300px;
    text-align: center;
    font-family: "Cinzel", Georgia, serif; font-weight: 400;
    font-size: 64px; color: var(--navy); letter-spacing: 1px;
  }
  .event {
    position: absolute; left: 20px; width: 430px; text-align: center;
    color: var(--navy);
  }
  .event-title {
    top: 290px;
    font-family: "Cinzel", Georgia, serif; font-weight: 400;
    font-size: 56px; line-height: 65px;
  }
  .event-title .accent { color: var(--orange-deep); font-size: 54px; }
  .label-row {
    display: flex; align-items: center; justify-content: center; gap: 10px;
    font-family: "Cinzel", Georgia, serif; font-size: 12px; color: var(--orange);
  }
  .label-row::before, .label-row::after {
    content: ""; width: 150px; height: 3px;
    background: linear-gradient(90deg, transparent, var(--navy) 30%, var(--navy) 70%, transparent);
  }
  .event-date { top: 520px; }
  .event-date .value {
    font-family: "Cinzel", Georgia, serif; font-size: 29px; margin: 2px 0 4px;
  }
  .event-date .time {
    font-family: "Cinzel", Georgia, serif; font-size: 19px; margin-top: 0;
  }
  .venue { top: 660px; font-size: 15.5px; line-height: 21px; font-style: normal; }
  .venue svg { display: block; margin: 0 auto 16px; }
  .contact {
    position: absolute; left: 80px; top: 874px; color: var(--white);
    list-style: none;
  }
  .contact li { display: flex; align-items: center; gap: 10px; height: 31px; font-size: 15px; }
  .contact li.phone { font-size: 24px; font-weight: 900; }
  .contact svg { flex: none; }
  .activities {
    position: absolute; left: 441px; top: 300px; width: 268px;
    list-style: none; text-align: center; color: var(--white); font-size: 16px;
  }
  .activities li { height: 116px; }
  .activities svg { display: block; margin: 0 auto 8px; }
  .tagline {
    position: absolute; left: 441px; top: 920px; width: 268px; text-align: center;
    font-style: italic; font-weight: 700;
  }
  .tagline .lead { color: var(--white); font-size: 14.5px; }
  .tagline .creed { color: var(--navy); font-size: 20px; font-weight: 900; margin-top: 2px; }
</style>
</head>
<body>
<main class="flyer">
  <svg class="flyer-shapes" viewBox="0 0 709 996" width="709" height="996" aria-hidden="true">
    <defs>
      <linearGradient id="dawn" x1="0" y1="0" x2="0" y2="1">
        <stop offset="0" stop-color="#f59a1d"/>
        <stop offset="0.5" stop-color="#f8b61f"/>
        <stop offset="1" stop-color="#f08a16"/>
      </linearGradient>
      <linearGradient id="hall" x1="0" y1="0" x2="1" y2="1">
        <stop offset="0" stop-color="#f6ede0"/>
        <stop offset="0.5" stop-color="#fbf8f3"/>
        <stop offset="1" stop-color="#efdcc4"/>
      </linearGradient>
      <radialGradient id="disc" cx="0.45" cy="0.4" r="0.7">
        <stop offset="0" stop-color="#ffffff"/>
        <stop offset="1" stop-color="#e3e3e3"/>
      </radialGradient>
      <linearGradient id="glow" x1="0" y1="0" x2="1" y2="1">
        <stop offset="0" stop-color="#f48a1e"/>
        <stop offset="1" stop-color="#e9640f"/>
      </linearGradient>
    </defs>
    <rect x="0" y="0" width="709" height="280" fill="url(#dawn)" role="img" aria-label="Sunrise sky with doves in flight"/>
    <path d="M0,215 C100,180 230,185 340,255 C380,280 420,295 441,296 L441,900 L0,900 Z" fill="url(#hall)" role="img" aria-label="Soft photo of a candlestick beside an open Bible"/>
    <rect x="441" y="230" width="268" height="766" fill="var(--navy)"/>
    <path d="M0,190 C100,150 230,160 340,230 C390,262 430,272 470,272 L470,300 C420,300 380,285 340,258 C230,188 100,185 0,220 Z" fill="var(--navy)"/>
    <path d="M0,190 C100,150 230,160 340,230 C390,262 430,272 470,272" fill="none" stroke="var(--white)" stroke-width="2"/>
    <circle cx="548" cy="80" r="204" fill="var(--orange-deep)"/>
    <circle cx="548" cy="80" r="190" fill="var(--white)"/>
    <circle cx="548" cy="80" r="185" fill="url(#disc)"/>
    <path d="M0,858 C120,812 260,808 420,852 C520,878 620,880 709,842 L709,996 L0,996 Z" fill="var(--orange)"/>
    <path d="M0,888 C120,846 260,842 420,884 C500,902 620,900 709,866 L709,996 L0,996 Z" fill="var(--navy)"/>
    <path d="M441,888 C510,903 620,900 709,866 L709,996 L441,996 Z" fill="url(#glow)" role="img" aria-label="Warm photo of hands folded in prayer"/>
    <path d="M420,884 C500,902 620,900 709,866" fill="none" stroke="var(--white)" stroke-width="1.5"/>
  </svg>

  <div class="brand">TOLVEX</div>

  <h1 class="event event-title">RADIANT<br>HARVEST<br><span class="accent">WORSHIP DAY</span></h1>

  <section class="event event-date">
    <div class="label-row">DATE</div>
    <p class="value">TUESDAY JULY 2ND, 2019</p>
    <div class="label-row">TIME</div>
    <p class="time">11:00AM - 7:00PM</p>
  </section>

  <address class="event venue">
    <svg width="30" height="30" viewBox="0 0 30 30" aria-hidden="true">
      <circle cx="15" cy="15" r="13.5" fill="none" stroke="var(--orange)" stroke-width="1.5"/>
      <path d="M15,8 a5,5 0 0 1 5,5 c0,4 -5,9 -5,9 c0,0 -5,-5 -5,-9 a5,5 0 0 1 5,-5 Z" fill="var(--orange)"/>
      <circle cx="15" cy="13" r="2" fill="var(--white)"/>
    </svg>
    Belmora Hotel, 4875 Wexley Avenue,<br>Portland, Maine 04102<br>(Room: Juniper)
  </address>

  <ul class="contact">
    <li class="phone">
      <svg width="20" height="20" viewBox="0 0 20 20" aria-hidden="true"><circle cx="10" cy="10" r="8.5" fill="none" stroke="var(--orange)" stroke-width="1.6"/><path d="M7,5.5 l2,2 -1,1.5 c.8,1.6 1.8,2.6 3,3 l1.5,-1 2,2 -1.5,1.5 c-3.5,-.3 -6.8,-3.6 -7.2,-7.2 Z" fill="var(--orange)"/></svg>
      207 555 3184
    </li>
    <li>
      <svg width="20" height="14" viewBox="0 0 20 14" aria-hidden="true"><rect x="0" y="0" width="20" height="14" fill="var(--orange)"/><path d="M0,0 L10,8 L20,0" fill="none" stroke="var(--navy)" stroke-width="1.5"/></svg>
      contact@brookhavenfold.org
    </li>
    <li>
      <svg width="18" height="18" viewBox="0 0 18 18" aria-hidden="true"><g fill="none" stroke="var(--orange)" stroke-width="1.5"><circle cx="9" cy="9" r="7.5"/><ellipse cx="9" cy="9" rx="3.2" ry="7.5"/><path d="M1.5,9 H16.5 M3,5 H15 M3,13 H15"/></g></svg>
      www.tolvex.org
    </li>
  </ul>

  <ul class="activities">
    <li>
      <svg width="60" height="60" viewBox="0 0 60 60" aria-hidden="true"><circle cx="30" cy="30" r="29" fill="var(--orange)" stroke="var(--white)" stroke-width="1.5"/><path d="M30,15 V40 M22,23 H38" stroke="var(--white)" stroke-width="4"/><path d="M16,34 l8,12 h12 l8,-12" fill="none" stroke="var(--white)" stroke-width="2.5"/></svg>
      Prayer
    </li>
    <li>
      <svg width="60" height="60" viewBox="0 0 60 60" aria-hidden="true"><circle cx="30" cy="30" r="29" fill="var(--orange)" stroke="var(--white)" stroke-width="1.5"/><g fill="var(--white)"><circle cx="30" cy="21" r="4.5"/><circle cx="18" cy="25" r="3.5"/><circle cx="42" cy="25" r="3.5"/><rect x="25.5" y="27" width="9" height="17" rx="3"/><rect x="15" y="30" width="6.5" height="13" rx="3"/><rect x="38.5" y="30" width="6.5" height="13" rx="3"/></g></svg>
      Sharing the Word
    </li>
    <li>
      <svg width="60" height="60" viewBox="0 0 60 60" aria-hidden="true"><circle cx="30" cy="30" r="29" fill="var(--orange)" stroke="var(--white)" stroke-width="1.5"/><g fill="var(--white)"><rect x="13" y="14" width="14" height="9" rx="2"/><rect x="33" y="14" width="14" height="9" rx="2"/><rect x="16" y="36" width="28" height="10"/><circle cx="22" cy="30" r="3"/><circle cx="30" cy="30" r="3"/><circle cx="38" cy="30" r="3"/></g></svg>
      Panel discussion
    </li>
    <li>
      <svg width="60" height="60" viewBox="0 0 60 60" aria-hidden="true"><circle cx="30" cy="30" r="29" fill="var(--orange)" stroke="var(--white)" stroke-width="1.5"/><circle cx="30" cy="32" r="13" fill="none" stroke="var(--white)" stroke-width="3"/><path d="M30,12 V46 M24,18 H36" stroke="var(--white)" stroke-width="3"/></svg>
      Prophecy
    </li>
    <li>
      <svg width="60" height="60" viewBox="0 0 60 60" aria-hidden="true"><circle cx="30" cy="30" r="29" fill="var(--orange)" stroke="var(--white)" stroke-width="1.5"/><g fill="none" stroke="var(--white)" stroke-width="2.5"><rect x="19" y="24" width="22" height="18"/><rect x="17" y="19" width="26" height="5"/><path d="M30,19 V42 M30,19 c-4,-6 -9,-3 -6,0 M30,19 c4,-6 9,-3 6,0"/></g></svg>
      Impartation
    </li>
  </ul>

  <div class="tagline">
    <p class="lead">A one day prayer retreat.</p>
    <p class="creed">Jesus Chris is Lord</p>
  </div>
</main>
</body>
</html>
```